Icon Design Project

Icon design for mobile site.

Site under development – viewable on pc or mobile at www.go.trellix.net/harborlane

Main site
www.harborlanesupport.co.uk
The branding is to be extended from the main site to the mobile site.

The site is nearly ready. I just need icons and buttons designed. If you visit www.go.trellix.net/harborlane you’ll see that I currently have text links instead of buttons. Looking at the site will help you understand where they go on the site.

Main menu icon set:
- ‘Special Offer’ button (not using Special Offer Image)
- ‘Services’ button
- ‘Contact’ button
- ‘Coffee?’ button
- ‘Video’ button

Category buttons.
These buttons need to integrate images with text. So that the buttons have image+text+border. All images provided with brief. Please go to www.harborlanesupport.co.uk to see how the main site uses them

These buttons should be large – covering nearly the entire width of the mobile page.

Buttons + Text as follows
Special Offer
Online Services
Local Marketing
Organisational Support
Tracking and Reporting
Websites
Mobile Sites
Training Portals
Local Search Optimisation
Call Tracking
SMS Campaigns
QR Campaigns
Mobile Ad Campaigns
Email Marketing
Social Media and Location Marketing
Tracking and Reporting

Please provide final buttons as transparent png/jpg.
Updates

Hi,

Thank you all for getting involved.

Some more detail on what I want.

The top menu: Special Offer - Services - Coffee - Contact, should be the width of the screen. Underneath should be a different looking video button.

Please make the top menu: Special Offer - Services - Coffee? - Contact buttons square with the text under an icon reflecting the buttons function. Graphically they need to stand out so don't feel you have to use the same grey as the menu on the main site (see brief for URL).

The video button can be longer and cover 1/3 to 1/2 the screen. This button should look different to the top menu buttons.

Hope this helps.

Marguerite

Dear all,

Looking forward to seeing your designs. Hope they come in quick so I can give you some feedback.

S

Target Market(s)

Businesses

Industry/Entity Type

Marketing

Requirements
Must have
• Must be in empathy with the design and colours found on site

```html
<!DOCTYPE html>
<html lang="en">
<head>
<meta charset="utf-8">
<title>Special Offer Button</title>
<link rel="stylesheet" href="https://fonts.googleapis.com/css2?family=Open+Sans:wght@400&display=swap">
<style>
  :root {
    --offer-red: #d40000;
    --backdrop-black: #000000;
    --label-white: #ffffff;
  }
  html, body {
    margin: 0;
    padding: 0;
    overflow: hidden;
    background: var(--label-white);
  }
  .offer-button {
    position: relative;
    width: 1117px;
    height: 1200px;
    overflow: hidden;
    background: var(--label-white);
  }
  .offer-button__field {
    position: absolute;
    left: 0;
    top: 0;
    width: 1117px;
    height: 976px;
    background: var(--backdrop-black);
  }
  .offer-button__heart {
    position: absolute;
    left: 0;
    top: 0;
    width: 1117px;
    height: 976px;
    display: block;
  }
  .offer-button__heart path {
    fill: var(--offer-red);
  }
  .offer-button__label {
    position: absolute;
    left: 0;
    top: 976px;
    width: 1117px;
    height: 224px;
    margin: 0;
    text-align: center;
    font-family: "Open Sans", Arial, sans-serif;
    font-weight: 400;
    font-size: 146px;
    line-height: 196px;
    letter-spacing: -1px;
    color: var(--offer-red);
  }
</style>
</head>
<body>
  <main class="offer-button">
    <div class="offer-button__field">
      <svg class="offer-button__heart" viewBox="0 0 838 732" preserveAspectRatio="none" aria-hidden="true">
        <path d="M419,130 C370,60 300,5 210,5 C150,5 110,22 95,32 C30,80 0,150 0,210 C0,400 200,560 421,732 C640,560 838,400 838,210 C838,150 808,80 742,32 C728,22 690,5 628,5 C540,5 470,60 419,130 Z"/>
      </svg>
    </div>
    <h1 class="offer-button__label">Special Offer</h1>
  </main>
</body>
</html>
```